5 x Packaging Design - Most of the design style is already done!

The logo is "Ember Over Tide" which will remain the same. The font is Athens.

We just require realistic packaging design with the fronts of the packaging. Together/ seperate/ in different mockup backdrops etc.

CLAY MASKS: BLACK JAR WHITE LID:
- the cursive coloured font is "Majesty"
- If you think you can design something even more attractive go for it! but we like the design a lot.
- Most important for us is to make it look realistic on the packaging so that we can use it on the website :)

BEARD OIL: BLACK JAR WITH SILVER AND WHITE PUMP LID:
- You are free to design similar/same or completely different

competitors:
Morvelle
reedandmoss

Industry/Entity Type

Cosmetics

```html
<!DOCTYPE html>
<html lang="en">
<head>
<meta charset="UTF-8">
<title>Ember Over Tide – Phoenix Rose Green Clay Mask Label</title>
<link rel="stylesheet" href="https://fonts.googleapis.com/css2?family=Josefin+Sans:wght@300&family=Advent+Pro:wght@300;400&family=Permanent+Marker&family=Caveat+Brush&display=swap">
<style>
  :root {
    --backdrop: #e4e3e8;
    --label-black: #15141b;
    --label-edge: #23222c;
    --ink-white: #f4f4f6;
    --ink-soft: #d9d8de;
    --accent-red: #e8344f;
  }
  html, body {
    margin: 0;
    padding: 0;
    width: 1200px;
    height: 675px;
    overflow: hidden;
    background: var(--backdrop);
  }
  .canvas {
    position: relative;
    width: 1200px;
    height: 675px;
    display: flex;
    align-items: center;
    justify-content: center;
  }
  .label {
    position: relative;
    width: 580px;
    height: 420px;
    background: var(--label-black);
    border: 1px solid var(--label-edge);
    border-radius: 6px;
    display: flex;
    flex-direction: column;
    align-items: center;
    box-sizing: border-box;
    padding-top: 70px;
  }
  .brand-name {
    margin: 0;
    font-family: "Josefin Sans", sans-serif;
    font-weight: 300;
    font-size: 31px;
    letter-spacing: 0.36em;
    color: var(--ink-white);
    text-transform: uppercase;
    padding-left: 0.36em;
    white-space: nowrap;
  }
  .product-name {
    margin: 30px 0 0 20px;
    font-family: "Permanent Marker", "Caveat Brush", cursive;
    font-weight: 400;
    font-size: 42px;
    line-height: 0.95;
    color: var(--accent-red);
    text-align: center;
    text-transform: uppercase;
    transform: rotate(-8deg);
    white-space: nowrap;
  }
  .product-type {
    margin: 18px 0 0;
    font-family: "Advent Pro", sans-serif;
    font-weight: 400;
    font-size: 19px;
    line-height: 1.4;
    letter-spacing: 0.26em;
    color: var(--ink-soft);
    text-align: center;
    text-transform: uppercase;
    padding-left: 0.26em;
  }
  .product-benefit {
    margin: 4px 0 0;
    font-family: "Advent Pro", sans-serif;
    font-weight: 300;
    font-size: 13px;
    line-height: 1.2;
    letter-spacing: 0.22em;
    color: var(--ink-soft);
    text-align: center;
    text-transform: uppercase;
  }
  .product-volume {
    margin: 6px 0 0;
    font-family: "Advent Pro", sans-serif;
    font-weight: 300;
    font-size: 11px;
    letter-spacing: 0.14em;
    color: var(--ink-soft);
    text-transform: uppercase;
  }
</style>
</head>
<body>
  <main class="canvas">
    <section class="label">
      <h1 class="brand-name">Ember Over Tide</h1>
      <p class="product-name">Phoenix<br>Rose</p>
      <p class="product-type">Green<br>Clay Mask</p>
      <p class="product-benefit">Moisturising and<br>Skin Rejuvenating</p>
      <p class="product-volume">50ml</p>
    </section>
  </main>
</body>
</html>
```